Etiketten-Design für nachhaltige Rasur- & Pflegeprodukte
> Wir suchen Verpackung und Etiketten für eine Marke für nachhaltige Rasur- & Pflegeprodukte.
Habedere liebe Designer,
„Habedere“ sagt man bei uns in Bayern, es bedeutet Hallo oder auf Wiedersehen, je nach Gelegenheit. In diesem Fall: Hallo.
Vielleicht kennst du uns schon, wir sind greenpines, wir betreiben einen kleinen Shop für Bartpflege & Rasur unter greenpines-shop.de und wir versuchen uns nun an einem neuen Thema: nachhaltige Rasur- & Pflegeprodukte für Frauen.
Das machen wir unter dem Namen „Kelva“.
Weil die Frage schon oft aufkam: Jawohl, wir haben uns dafür die Beine und die Achseln mit einem Rasierhobel rasiert.
> Zielgruppe.
Wir arbeiten an einer neuen Pflegelinie für Frauen, die sich vorwiegend mit der Rasur und den dazugehörigen Pflegeprodukten beschäftigt. Die Zielgruppe sind vor allem online-affine Frauen aus Deutschland, Österreich und der Schweiz, aber sicher auch europaweit im Alter von 21-45.
> Aufgabenstellung.
Wir sind auf der Suche nach einem Konzept für unsere Produktverpackungen bzw. Etiketten. Bei den Pflegeprodukten verzichten wir bewusst auf eine Umverpackung.
Konkret geplant sind ein Rasierhobel, dafür haben wir eine schöne Umverpackung. Außerdem starten wir mit Rasieröl, Rasierseife und einem After Shave Balsam. Es werden später noch andere Artikel dazukommen, eine Deocreme zum Beispiel.
Rasieröl, Rasiercreme und After Shave Balsam duften nach Orangen, es werden zwei oder drei weitere Duftrichtungen folgen, die eine wird beispielsweise nach Beeren duften, die andere nach Pfirsich und Mango – bitte beachte das bei der Erstellung des Konzeptes, die Unterschiede sollten später auf den ersten Blick erkennbar sein.
Zurück zum Thema Orange: Wir würden den Duft als leicht herben Zitrusduft bezeichnen.
> Die Maße.
• Umverpackung Rasierhobel, weißer Karton (165x90x40mm)
• Rasieröl 30ml (Etikett: 100x46mm)
• Rasiercreme 60ml (Etikett: 156x32mm)
• After Shave Balsam 60ml (Etikett: 156x32mm)
> Zwingend erforderliche Angaben.
Da es sich um Kosmetikprodukte handelt, sind einige Angaben auf dem Label zwingend erforderlich, beispielhaft sollen die folgenden Infos als Platzhalter dienen.
• Hergestellt für Friedrich Lautner e.K. von greenpines, Lindenhofweg 7, 83109 Kolbermoor
• Ingredients: Aqua, Stearic Acid, Cocos Nucifera oil, Glycerin, Potassium Hydroxide, Litsea Cubeba oil, (and) Citrus Sinensis Peel oil, Orbignya Oleifera oil, Sodium Hydroxide, Macadamia ternifolia oil, Talc, Kaolin, Citric Acid, Simmondsia chinensis oil, Maris sal, C.I. 77892 (and) Rad Clay, Citral, Limonene, Linalool, Geraniol
• Platz für einen Barcode
• Rasieröl sind 30ml / 1.01 FL.OZ. ODER Creme & Balsam jeweils 60ml / 2.03 FL. OZ.
Wir haben ein Bild der aktuellen Gefäße beigefügt, es kann aber durchaus sein, dass wir uns noch umen..

```html
<!DOCTYPE html>
<html lang="de">
<head>
<meta charset="utf-8">
<title>Kelva – Etikett und Umverpackung</title>
<link rel="stylesheet" href="https://fonts.googleapis.com/css2?family=Oswald:wght@300;400&display=swap">
<style>
  :root {
    --bg: #dcdcdc;
    --paper: #f4f4f3;
    --ink: #2c2c2c;
    --ink-soft: #6a6a6a;
    --rule: #c4c4c4;
    --scent-orange: #efe3b6;
    --scent-mark: #e2d199;
  }
  * { margin: 0; padding: 0; box-sizing: border-box; }
  html, body { width: 1200px; height: 960px; overflow: hidden; }
  body {
    background: var(--bg);
    font-family: "Oswald", "Arial Narrow", sans-serif;
    font-weight: 300;
    color: var(--ink);
    position: relative;
  }
  .brand { display: flex; align-items: center; justify-content: center; }
  .brand-name { font-weight: 300; letter-spacing: .3em; color: var(--ink); text-transform: uppercase; }

  /* Flaschenetikett */
  .label {
    position: absolute; left: 60px; top: 330px; width: 560px; height: 300px;
    background: var(--paper); border: 1px solid var(--rule);
    display: grid; grid-template-rows: 170px 1fr;
  }
  .label .brand-name { font-size: 18px; }
  .label-info {
    border-top: 1px solid var(--rule);
    display: grid; grid-template-columns: 46px 1fr 150px;
  }
  .label-code { border-right: 1px solid var(--rule); }
  .label-main { display: grid; grid-template-rows: 44px 38px 1fr; }
  .product-name { text-align: center; font-size: 15px; letter-spacing: .22em; align-self: center; }
  .scent-band {
    display: grid; grid-template-columns: 40px 1fr 36px; align-items: center;
    background: var(--scent-orange); margin-right: 10px;
  }
  .scent-number { font-size: 11px; text-align: center; border-right: 1px solid #d6c98f; height: 100%; display: flex; align-items: center; justify-content: center; }
  .scent-name { text-align: center; font-size: 12px; letter-spacing: .08em; }
  .scent-mark { width: 22px; height: 22px; border-radius: 50%; background: var(--scent-mark); }
  .label-foot { display: grid; grid-template-columns: 64px 1fr; font-size: 9.5px; line-height: 1.35; color: var(--ink); }
  .volume { border-right: 1px solid var(--rule); padding: 8px 6px; color: var(--ink-soft); }
  .description { padding: 8px 10px; color: var(--ink); }
  .label-side { border-left: 1px solid var(--rule); display: grid; grid-template-rows: 1fr 1fr; }
  .side-block { display: grid; grid-template-columns: 14px 1fr; gap: 4px; padding: 6px; font-size: 8px; line-height: 1.3; color: var(--ink-soft); }
  .side-block + .side-block { border-top: 1px solid var(--rule); }
  .side-title { writing-mode: vertical-rl; transform: rotate(180deg); font-size: 7px; letter-spacing: .12em; }

  /* Umverpackung Rasierhobel */
  .box {
    position: absolute; left: 770px; top: 140px; width: 360px; height: 680px;
    background: var(--paper); border: 1px solid var(--rule);
    display: grid; grid-template-rows: 64px 330px 96px 70px 1fr;
  }
  .box > * { border-bottom: 1px solid var(--rule); }
  .box-flap { background: #ececeb; }
  .box-logo { display: flex; align-items: flex-start; justify-content: center; padding-top: 110px; }
  .box-logo .brand-name { font-size: 22px; }
  .box-title { display: flex; align-items: center; justify-content: center; font-size: 24px; font-weight: 400; letter-spacing: .2em; }
  .box-details { display: grid; grid-template-columns: 44px 1fr 64px 56px; }
  .box-details > * + * { border-left: 1px solid var(--rule); }
  .box-number { writing-mode: vertical-rl; transform: rotate(180deg); display: flex; align-items: center; justify-content: center; font-size: 13px; }
  .box-text { font-size: 10px; letter-spacing: .08em; padding: 10px; }
  .box-item { display: flex; flex-direction: column; align-items: center; justify-content: center; gap: 4px; font-size: 10px; }
  .item-figure { width: 16px; height: 34px; background: #d3d3d2; }
  .item-figure.blade { width: 18px; height: 26px; }
  .box-base { border-bottom: none; display: flex; align-items: flex-end; justify-content: center; padding-bottom: 28px; }
  .box-base .brand-name { font-size: 12px; }
</style>
</head>
<body>

<section class="label" aria-label="Etikett Rasiercreme Orange-Zitrus">
  <div class="brand"><span class="brand-name">Kelva</span></div>
  <div class="label-info">
    <div class="label-code"></div>
    <div class="label-main">
      <p class="product-name">PRODUKT</p>
      <div class="scent-band">
        <span class="scent-number">No 6</span>
        <span class="scent-name">ORANGE-ZITRUS</span>
        <span class="scent-mark" role="img" aria-label="Symbol Orangenscheibe"></span>
      </div>
      <div class="label-foot">
        <p class="volume">2.03 FL. OZ. /<br>60ml ℮</p>
        <p class="description">Blindtext Pflegt und beruhigt deine Haut während der Rasur und spendet extra viel Feuchtigkeit Blindtext</p>
      </div>
    </div>
    <div class="label-side">
      <div class="side-block"><span class="side-title">INGREDIENTS</span><p>Ingredients: Aqua, Stearic Acid, Cocos Nucifera oil, Glycerin</p></div>
      <div class="side-block"><span class="side-title">ANWENDUNG</span><p>Anwendung: Auf feuchte Haut auftragen, sanft einmassieren.</p></div>
    </div>
  </div>
</section>

<section class="box" aria-label="Umverpackung Rasierhobel">
  <div class="box-flap"></div>
  <div class="box-logo">
    <div class="brand"><span class="brand-name">Kelva</span></div>
  </div>
  <h1 class="box-title">RASIERHOBEL</h1>
  <div class="box-details">
    <span class="box-number">No 1</span>
    <p class="box-text">BLIDTEXT ZU RASIERHOBEL BLINDTEXT</p>
    <div class="box-item"><span class="item-figure" role="img" aria-label="Symbol Rasierhobel"></span>1x</div>
    <div class="box-item"><span class="item-figure blade" role="img" aria-label="Symbol Rasierklinge"></span>5x</div>
  </div>
  <div class="box-base">
    <div class="brand"><span class="brand-name">Kelva</span></div>
  </div>
</section>

</body>
</html>
```